Vornel Wellness Business Card

A Double Sided Business Card

I am a private company in Melbourne, Australia, working in the Health industry. I am a nutritionist and lifestyle coach, whom specialises in using raw foods ie. fruits/nuts/vegetables to help heal my clients and enable them to achieve their ultimate state of health.

I want a sophisticated design and colour for my card that appeals to both men and women from teenage through to elderly.

Front of Card:

Red apple peel spiral in the shape of an apple. I would like a leaf/leaves coming off the stem of the apple. Please see attachments for example.

***On Right Hand side of Image is business Name: Vornel Wellness

Underneath LOGO use slogan " Let Food Be Your Medicine"

***Use Deep Red and Blues for Text Colouring

Back of Card:

Marisol Dekkert
Nutritional Specialist and Lifestyle Coach

Specialising in: Diseased Conditions
Weight Management
Achieving your Ultimate State of Health

enquiries@vornelwellness.com.au 0457 396 504

**Make sure the front design of the card flows onto the back.
Updates

Email address has been amended, Also more specific details have been given for apple peel Image, and another image attached as example of Leaf on stem of apple.

I little more insight into what sort of feel were trying to create. We're apart of the health industry, and we want the card to have a medical/clinical feeling about it.

Target Market(s)

Males and Females from teenages to elderly

Industry/Entity Type

Business

Requirements
Must have
• Red Apple Peel Spiral, in the shape of an apple, with a leaf/leaves attached to stem.
***Must be in the shape of an apple
***Please use coloring on inside of apple peel to resemble inside of an apple.
Nice to have
• I would like my card to have a clinical feel.
Should not have
• We don't want the image of the apple to look like a Christmas decoration

```html
<!DOCTYPE html>
<html lang="en">
<head>
<meta charset="utf-8">
<title>Vornel Wellness – Business Card Back</title>
<link rel="stylesheet" href="https://fonts.googleapis.com/css2?family=Quicksand:wght@400;500;600&display=swap">
<style>
  :root {
    --card-white: #ffffff;
    --card-mist: #e4e4e6;
    --brand-red: #c4161c;
    --brand-red-deep: #9e0f14;
    --ink-grey: #6d6e71;
    --ink-grey-soft: #a7a9ac;
    --navy: #1c2a6b;
    --royal: #3a4fb0;
    --footer-black: #231f20;
    --footer-text: #ffffff;
  }
  * { margin: 0; padding: 0; box-sizing: border-box; }
  html, body { width: 1200px; height: 740px; overflow: hidden; }
  body { font-family: "Quicksand", sans-serif; background: var(--card-white); }

  .card {
    position: relative;
    width: 1200px;
    height: 740px;
    overflow: hidden;
    background: radial-gradient(ellipse at 45% 40%, var(--card-white) 40%, var(--card-mist) 100%);
  }

  .accent-bars { position: absolute; left: 40px; top: 0; display: flex; gap: 10px; }
  .accent-bars span {
    display: block; width: 17px; height: 258px;
    background: linear-gradient(90deg, var(--brand-red-deep), var(--brand-red) 50%, var(--brand-red-deep));
  }

  .identity { position: absolute; left: 126px; top: 118px; }
  .identity__name {
    font-weight: 400; font-size: 57px; line-height: 1; color: var(--brand-red);
    letter-spacing: 0.5px;
  }
  .identity__role { position: relative; margin-top: 8px; padding-left: 44px; }
  .identity__amp {
    position: absolute; left: -4px; top: -8px;
    font-size: 92px; font-weight: 500; line-height: 1; color: var(--ink-grey-soft);
  }
  .identity__line {
    position: relative; font-size: 38px; font-weight: 500; line-height: 40px; color: var(--ink-grey);
  }

  .specialties { position: absolute; left: 124px; top: 322px; }
  .specialties__heading {
    font-size: 43px; font-weight: 500; line-height: 1; margin-bottom: 12px;
    background: linear-gradient(90deg, var(--navy), var(--royal));
    -webkit-background-clip: text; background-clip: text; color: transparent;
  }
  .specialties__list { list-style: none; }
  .specialties__item {
    font-size: 34px; font-weight: 400; line-height: 47px; color: var(--ink-grey);
  }

  .apple-artwork {
    position: absolute; left: 800px; top: 120px; width: 340px; height: 430px;
    background:
      radial-gradient(ellipse 48% 38% at 50% 36%, var(--brand-red) 0%, var(--brand-red) 55%, rgba(196,22,28,0.55) 75%, rgba(255,255,255,0) 100%),
      radial-gradient(ellipse 40% 18% at 50% 82%, rgba(196,22,28,0.12), rgba(255,255,255,0));
  }

  .contact-bar {
    position: absolute; left: 0; bottom: 0; width: 1200px; height: 177px;
    background: var(--footer-black);
    padding: 26px 0 0 48px;
  }
  .contact-bar__row { display: flex; align-items: center; height: 60px; }
  .contact-bar__icon { width: 54px; height: 54px; flex: none; margin-right: 22px; }
  .contact-bar__text { font-size: 38px; font-weight: 500; color: var(--footer-text); }
</style>
</head>
<body>
<main class="card">
  <div class="accent-bars" aria-hidden="true"><span></span><span></span><span></span></div>

  <header class="identity">
    <h1 class="identity__name">Marisol Dekkert</h1>
    <div class="identity__role">
      <span class="identity__amp" aria-hidden="true">&amp;</span>
      <p class="identity__line">Nutritional Specialist</p>
      <p class="identity__line">Lifestyle Coach</p>
    </div>
  </header>

  <section class="specialties">
    <h2 class="specialties__heading">Specialising in:</h2>
    <ul class="specialties__list">
      <li class="specialties__item">Diseased Conditions</li>
      <li class="specialties__item">Weight Management</li>
      <li class="specialties__item">Achieving your Ultimate State of Health</li>
    </ul>
  </section>

  <div class="apple-artwork" role="img" aria-label="Red apple peel spiral shaped like an apple, with its soft reflection below"></div>

  <footer class="contact-bar">
    <div class="contact-bar__row">
      <svg class="contact-bar__icon" viewBox="0 0 54 54" aria-hidden="true">
        <circle cx="27" cy="27" r="26" fill="var(--brand-red)" stroke="#e8e8e8" stroke-width="2"/>
        <g fill="none" stroke="#fff" stroke-width="2">
          <circle cx="27" cy="27" r="13"/>
          <ellipse cx="27" cy="27" rx="6" ry="13"/>
          <line x1="14" y1="27" x2="40" y2="27"/>
          <path d="M16 20h22M16 34h22"/>
        </g>
      </svg>
      <span class="contact-bar__text">info@vornelwellness.com.au</span>
    </div>
    <div class="contact-bar__row">
      <svg class="contact-bar__icon" viewBox="0 0 54 54" aria-hidden="true">
        <circle cx="27" cy="27" r="26" fill="var(--brand-red)" stroke="#e8e8e8" stroke-width="2"/>
        <path fill="#fff" d="M19 13c2-1 3 0 4 1l3 5c1 2 0 3-1 4l-2 1c1 3 4 6 7 8l1-2c1-1 2-2 4-1l5 3c1 1 2 2 1 4l-2 3c-2 2-5 2-8 0-6-3-11-8-14-14-2-3-2-6 0-8z"/>
      </svg>
      <span class="contact-bar__text">0457 396 504</span>
    </div>
  </footer>
</main>
</body>
</html>
```